Creative, fresh business card design for Ripplecraft Facades

We need a fresh, creative business card design for Ripplecraft Facades. We are the manufacturer of Ripplecraft Facades in Australia. Wall panels are 2400 x 1200mm panels made from MDF and feature 3D patterns on the face of the panel. The colours to be used are green, silver/grey and white RGB
Red 187
Green 207
Blue 65.

An idea is to possibly use a watermark of one of our designs as a background (like on the "Grids" design on the left hand side of page 2 of our brochure).

Target Market(s)

Interior designers, architects, builders and home renovators

Industry/Entity Type

Business

Contact Information for Business Card

Details to go on the card are:
Our logo (attached),
Slogan: "Decorative panels for interiors and exteriors",
Contact name,
Position,
Mobile phone number,
Business address,
Business phone,
Business fax,
Website and
Email address.

I have attached a few images of our panels and our brochure for reference.

The colours of the business card should feature our logo colours which are: RGB
Red 187
Green 207
Blue 65

Requirements
Must have
• Very modern fonts and design. Some of the designs shown especially the "Prisms" design which is a popular design.
Nice to have
• Creative but simple design. Very contemporary.
Should not have
• Anything ornate or old fashioned.

```html
<!DOCTYPE html>
<html lang="en">
<head>
<meta charset="utf-8">
<title>Ripplecraft Facades – Business Card</title>
<link rel="stylesheet" href="https://fonts.googleapis.com/css2?family=Arimo:wght@400;700&display=swap">
<style>
  :root {
    --page-bg: #d9d6d1;
    --card-bg: #eeedea;
    --brand-green: rgb(187, 207, 65);
    --brand-green-light: #c9dc5e;
    --brand-green-deep: #8fae1e;
    --band-grey: #6f6e6c;
    --ink-dark: #4a4a4a;
    --ink-light: #ffffff;
    --ink-soft: #f1f5dc;
    --ink-band: #d8d8d6;
  }
  * { margin: 0; padding: 0; box-sizing: border-box; }
  html, body {
    width: 1200px;
    height: 969px;
    overflow: hidden;
    background: var(--page-bg);
    font-family: "Arimo", Arial, sans-serif;
  }
  .business-card {
    position: absolute;
    left: 100px;
    top: 200px;
    width: 1000px;
    height: 570px;
    background: var(--card-bg);
    overflow: hidden;
  }
  .contact-panel {
    position: absolute;
    left: 0;
    top: 0;
    width: 480px;
    height: 570px;
    background: linear-gradient(160deg, var(--brand-green-deep) 0%, var(--brand-green) 45%, var(--brand-green-light) 100%);
  }
  .person-name {
    position: absolute;
    left: 57px;
    top: 108px;
    font-size: 32px;
    font-weight: 700;
    letter-spacing: 1px;
    color: var(--ink-light);
  }
  .person-role {
    position: absolute;
    left: 57px;
    top: 152px;
    font-size: 26px;
    color: var(--ink-light);
  }
  .address {
    position: absolute;
    left: 57px;
    top: 206px;
    font-size: 25px;
    line-height: 38px;
    color: var(--ink-light);
    font-style: normal;
  }
  .contact-list {
    position: absolute;
    left: 57px;
    top: 292px;
    list-style: none;
  }
  .contact-item {
    display: flex;
    align-items: center;
    height: 39px;
    font-size: 24px;
    color: var(--ink-soft);
  }
  .contact-icon {
    width: 22px;
    height: 22px;
    margin-right: 19px;
    fill: var(--ink-light);
    flex: none;
  }
  .web-band {
    position: absolute;
    left: 0;
    top: 478px;
    width: 480px;
    height: 92px;
    background: var(--band-grey);
    display: flex;
    align-items: center;
    padding-left: 57px;
    font-size: 25px;
    letter-spacing: 2px;
    color: var(--ink-band);
  }
  .brand-block {
    position: absolute;
    left: 540px;
    top: 215px;
    width: 420px;
    display: flex;
    flex-direction: column;
    align-items: center;
  }
  .brand-lockup {
    display: flex;
    align-items: center;
    gap: 16px;
  }
  .brand-square {
    width: 54px;
    height: 54px;
    background: var(--brand-green);
    flex: none;
  }
  .brand-name {
    font-size: 32px;
    font-weight: 700;
    line-height: 1.1;
    white-space: nowrap;
    color: var(--ink-dark);
  }
  .brand-tagline {
    margin-top: 44px;
    font-size: 20px;
    line-height: 33px;
    letter-spacing: 3.5px;
    text-align: center;
    color: var(--ink-dark);
  }
</style>
</head>
<body>
  <main class="business-card">
    <section class="contact-panel">
      <h1 class="person-name">MARA LINDQVIST</h1>
      <p class="person-role">CEO&amp;Founder</p>
      <address class="address">214 Wattle Grove Road<br>Geelong, Victoria 3220</address>
      <ul class="contact-list">
        <li class="contact-item">
          <svg class="contact-icon" viewBox="0 0 24 24" aria-hidden="true"><path d="M7 1h10a2 2 0 0 1 2 2v18a2 2 0 0 1-2 2H7a2 2 0 0 1-2-2V3a2 2 0 0 1 2-2zm0 3v14h10V4zm5 15.5a1.2 1.2 0 1 0 0 2.4 1.2 1.2 0 0 0 0-2.4z"/></svg>
          0412 738 905
        </li>
        <li class="contact-item">
          <svg class="contact-icon" viewBox="0 0 24 24" aria-hidden="true"><path d="M6.6 10.8a15.1 15.1 0 0 0 6.6 6.6l2.2-2.2c.3-.3.7-.4 1-.2 1.1.4 2.3.6 3.6.6.6 0 1 .4 1 1V20c0 .6-.4 1-1 1A17 17 0 0 1 3 4c0-.6.4-1 1-1h3.5c.6 0 1 .4 1 1 0 1.3.2 2.5.6 3.6.1.3 0 .7-.2 1z"/></svg>
          (03) 5281-4069
        </li>
        <li class="contact-item">
          <svg class="contact-icon" viewBox="0 0 24 24" aria-hidden="true"><path d="M6 2h12v5H6z"/><path d="M3 8h18a1 1 0 0 1 1 1v8h-4v-3H6v3H2V9a1 1 0 0 1 1-1z"/><path d="M7 15h10v7H7z"/></svg>
          (03) 5281-4070
        </li>
        <li class="contact-item">
          <svg class="contact-icon" viewBox="0 0 24 24" aria-hidden="true"><path d="M2 5h20v2l-10 6L2 7z"/><path d="M2 9l10 6 10-6v10H2z"/></svg>
          mara@ripplecraft.com.au
        </li>
      </ul>
      <div class="web-band">www.ripplecraft.com.au</div>
    </section>

    <section class="brand-block">
      <div class="brand-lockup">
        <span class="brand-square" aria-hidden="true"></span>
        <span class="brand-name">Ripplecraft Facades</span>
      </div>
      <p class="brand-tagline">decorative panels for<br>interiors and exteriors</p>
    </section>
  </main>
</body>
</html>
```